Business Card Design

Business Card for professional consulting firm working with large financial institutions.

Target Market(s)

Executive buyers

Industry/Entity Type

Banking

Contact Information for Business Card

Mild creativity wanted. Not boring, but do elaborate artwork.

Font styles to use
Serif
Sans Serif

Colors

Designer to choose colors to be used in the design.

Requirements
Must have
• Standard business card features - company name, individual name, telephone, website, email, locations.
Nice to have
• Two colors
Should not have
• too many colors, fancy printing, cartoons.

```html
<!DOCTYPE html>
<html lang="en">
<head>
<meta charset="utf-8">
<title>c4advisory business card</title>
<link rel="stylesheet" href="https://fonts.googleapis.com/css2?family=Roboto:wght@400;500&family=Roboto+Condensed:wght@500&display=swap">
<style>
  :root {
    --backdrop: #262626;
    --card: #f2f2f2;
    --ink: #1a1a1a;
    --ink-soft: #4a4a4a;
    --muted: #a6a6a6;
    --rule: #c8c8c8;
    --band-dark: #0d0d0d;
    --band-light: #c4c4c4;
    --band-text: #ffffff;
  }
  * { margin: 0; padding: 0; box-sizing: border-box; }
  html, body { width: 1200px; height: 960px; overflow: hidden; }
  body {
    background: var(--backdrop);
    position: relative;
    font-family: "Roboto", Arial, sans-serif;
  }
  .card {
    position: absolute;
    width: 600px;
    height: 343px;
    background: var(--card);
    box-shadow: 0 2px 6px rgba(0,0,0,.5);
  }
  .card--front { left: 314px; top: 113px; }
  .card--back { left: 311px; top: 472px; }

  .brand-name {
    position: absolute;
    font-family: "Roboto", Arial, sans-serif;
    font-weight: 400;
    color: var(--ink);
    white-space: nowrap;
    transform: translate(-50%, -50%);
  }
  .card--front .brand-name { left: 176px; top: 167px; font-size: 32px; }
  .card--back .brand-name { left: 300px; top: 165px; font-size: 40px; }

  .divider {
    position: absolute;
    left: 335px; top: 95px;
    width: 1px; height: 147px;
    background: var(--rule);
  }
  .contact {
    position: absolute;
    left: 365px; top: 100px;
    color: var(--ink-soft);
    font-size: 15px;
    line-height: 19px;
  }
  .contact__name {
    font-family: "Roboto Condensed", Arial, sans-serif;
    font-weight: 500;
    font-size: 22px;
    line-height: 24px;
    color: var(--ink);
  }
  .contact__title {
    font-family: "Roboto Condensed", Arial, sans-serif;
    font-weight: 500;
    font-size: 16px;
    line-height: 18px;
    color: var(--muted);
    margin-bottom: 19px;
  }
  .contact__address { margin-bottom: 9px; }
  .contact__line { display: flex; align-items: center; gap: 8px; }
  .contact__line svg { width: 13px; height: 13px; fill: var(--ink); }

  .web-band {
    position: absolute;
    left: 0; width: 600px; height: 29px;
    display: flex; align-items: center; justify-content: center;
    color: var(--band-text);
    font-size: 15px;
    letter-spacing: 5px;
  }
  .card--front .web-band { top: 280px; background: var(--band-dark); }
  .card--back .web-band { top: 276px; background: var(--band-light); }
</style>
</head>
<body>
  <section class="card card--front">
    <div class="brand-name">c4advisory</div>
    <div class="divider"></div>
    <div class="contact">
      <div class="contact__name">DANIEL REYES</div>
      <div class="contact__title">CEO/FOUNDER</div>
      <div class="contact__address">4120 Maple Crest Road<br>Juneau, Alaska 99801</div>
      <div class="contact__line">
        <svg viewBox="0 0 24 24" aria-hidden="true"><path d="M6.6 10.8a15.1 15.1 0 0 0 6.6 6.6l2.2-2.2c.3-.3.7-.4 1-.2 1.1.4 2.3.6 3.6.6.6 0 1 .4 1 1V20c0 .6-.4 1-1 1A17 17 0 0 1 3 4c0-.6.4-1 1-1h3.5c.6 0 1 .4 1 1 0 1.3.2 2.5.6 3.6.1.3 0 .7-.2 1z"/></svg>
        <span>555 214 0736</span>
      </div>
      <div class="contact__line">
        <svg viewBox="0 0 24 24" aria-hidden="true"><path d="M2 5h20v14H2z M3.5 6.5v.6l8.5 6 8.5-6v-.6z" fill-rule="evenodd"/></svg>
        <span>info@c4advisory.com</span>
      </div>
    </div>
    <div class="web-band">www.c4advisory.com</div>
  </section>

  <section class="card card--back">
    <div class="brand-name">c4advisory</div>
    <div class="web-band">www.c4advisory.com</div>
  </section>
</body>
</html>
```